New Bicycle shop business card

Hi!
I'm looking for a business card for my new proffesional bike mechanics shop. This shop is only for fixing broken bikes and not selling bikes.
Peferbly a modern and sleek and modern design.
Colors: black, grey, red, white
Information:
Name: Rijwielwerkplaats Vanhoutte
Shop owner: Bart Vanhoutte & Marieke Segers
Website: www.rijwielwerkplaats-vanhoutte.be
Email: info@rijwielwerkplaats-vanhoutte.be
Phone number: +32471902368
Street adres: Kerkweg 46
9940 Bellebeke
Slogan/shop information: Herstellingen van alle merken.
Logo: see files.
Target Market(s)
People who seek a mechanic to fix or upgrade their bikes.
Contact Information for Business Card
Information:
Website: info@rijwielwerkplaats-vanhoutte.be
9940 Bellebeke
Logo: see files.

```html
<!DOCTYPE html>
<html lang="nl">
<head>
<meta charset="utf-8">
<title>Rijwielwerkplaats Vanhoutte – Visitekaartje</title>
<link rel="stylesheet" href="https://fonts.googleapis.com/css2?family=Roboto:wght@400;500;700&display=swap">
<style>
  :root {
    --red: #e3263a;
    --ink: #1f1a17;
    --text: #222222;
    --card: #ffffff;
    --backdrop: #d9d9d9;
    --band-dark: #1e1412;
  }
  * { box-sizing: border-box; margin: 0; padding: 0; }
  html, body {
    width: 1200px; height: 909px; overflow: hidden;
    background: var(--backdrop);
    font-family: "Roboto", Arial, sans-serif;
    color: var(--text);
  }
  .canvas { position: relative; width: 1200px; height: 909px; }
  .card {
    position: absolute; width: 620px; height: 376px;
    background: var(--card);
    box-shadow: 0 6px 18px rgba(0,0,0,.18);
    overflow: hidden;
  }
  /* Front */
  .card--front { left: 80px; top: 70px; }
  .front-brand {
    position: absolute; left: 0; right: 0; top: 128px;
    display: flex; flex-direction: column; align-items: center; gap: 18px;
  }
  .brand-dot { width: 46px; height: 46px; border-radius: 50%; background: var(--red); }
  .brand-name {
    font-weight: 700; font-size: 30px; letter-spacing: 1px;
    color: var(--ink); text-align: center; line-height: 1.15;
  }
  /* Back */
  .card--back { left: 500px; top: 460px; }
  .back-brand {
    position: absolute; right: 26px; top: 24px;
    display: flex; align-items: center; gap: 8px;
    font-weight: 700; font-size: 13px; color: var(--ink);
  }
  .back-brand .brand-dot { width: 16px; height: 16px; }
  .contact { position: absolute; left: 50px; top: 138px; }
  .contact__name { color: var(--red); font-weight: 500; font-size: 23px; line-height: 1.1; }
  .contact__owners { font-size: 15px; margin-top: 4px; }
  .contact__address { font-size: 15px; line-height: 1.3; margin-top: 20px; }
  .contact__list { list-style: none; margin-top: 12px; font-size: 15px; }
  .contact__list li { display: flex; align-items: center; gap: 14px; line-height: 1.45; }
  .contact__list svg { width: 14px; height: 14px; fill: var(--red); flex: none; }
  .bands { position: absolute; left: 0; bottom: 0; width: 620px; height: 64px; }
  .slogan {
    position: absolute; right: 22px; bottom: 19px;
    color: #fff; font-size: 15px; font-weight: 400; line-height: 18px;
    white-space: nowrap;
  }
</style>
</head>
<body>
<div class="canvas">

  <section class="card card--front" aria-label="Voorzijde visitekaartje">
    <div class="front-brand">
      <div class="brand-dot"></div>
      <div class="brand-name">RIJWIELWERKPLAATS<br>VANHOUTTE</div>
    </div>
  </section>

  <section class="card card--back" aria-label="Achterzijde visitekaartje">
    <div class="back-brand"><span class="brand-dot"></span>Rijwielwerkplaats Vanhoutte</div>

    <div class="contact">
      <h1 class="contact__name">Rijwielwerkplaats Vanhoutte</h1>
      <p class="contact__owners">Shop owner: Bart Vanhoutte &amp; Marieke Segers</p>
      <p class="contact__address">Kerkweg 46<br>9940 Bellebeke</p>
      <ul class="contact__list">
        <li>
          <svg viewBox="0 0 24 24" aria-hidden="true"><path d="M6.6 10.8a15.1 15.1 0 0 0 6.6 6.6l2.2-2.2a1 1 0 0 1 1-.25 11.4 11.4 0 0 0 3.6.57 1 1 0 0 1 1 1V20a1 1 0 0 1-1 1A17 17 0 0 1 3 4a1 1 0 0 1 1-1h3.5a1 1 0 0 1 1 1c0 1.25.2 2.45.57 3.57a1 1 0 0 1-.25 1z"/></svg>
          +32471902368
        </li>
        <li>
          <svg viewBox="0 0 24 24" aria-hidden="true"><path d="M2 5h20v14H2z"/><path d="M2 5l10 8 10-8z" fill="#fff" opacity=".35"/></svg>
          info@rijwielwerkplaats-vanhoutte.be
        </li>
        <li>
          <svg viewBox="0 0 24 24" aria-hidden="true"><circle cx="12" cy="12" r="10"/><path d="M2 12h20M12 2c3 3 3 17 0 20M12 2c-3 3-3 17 0 20" stroke="#fff" stroke-width="1.5" fill="none"/></svg>
          www.rijwielwerkplaats-vanhoutte.be
        </li>
      </ul>
    </div>

    <svg class="bands" viewBox="0 0 620 64" aria-hidden="true">
      <rect x="0" y="52" width="620" height="12" fill="var(--band-dark)"/>
      <polygon points="376,20 620,20 620,52 362,52" fill="var(--red)"/>
    </svg>
    <p class="slogan">Herstellingen van alle merken.</p>
  </section>

</div>
</body>
</html>
```